Business Card Design

New business card design

Target Market(s)

Residential & Commercial Property Managers

Industry/Entity Type

Plumbing Services

Contact Information for Business Card

Name - Rowan Keddle, title - Director, Phone Number - 0431 286 517, email - rowan@tbk-plumbing.com.au, Company ABN - 73 215 904 386,

Font styles to use
Sans Serif

Colors
0054AA
0677BA
7BADD7
CADEEF
E8F1F8

```html
<!DOCTYPE html>
<html lang="en">
<head>
<meta charset="utf-8">
<title>TBK Plumbing Services – Business Card</title>
<link href="https://fonts.googleapis.com/css2?family=Roboto:wght@300;400;500;700&display=swap" rel="stylesheet">
<style>
  :root {
    --deep-blue: #0054AA;
    --mid-blue: #0677BA;
    --sky-blue: #7BADD7;
    --mist-blue: #CADEEF;
    --ice-blue: #E8F1F8;
    --bright-cyan: #1FA8E6;
    --navy: #063F86;
    --stage: #1c1c1e;
    --white: #ffffff;
  }
  * { box-sizing: border-box; margin: 0; padding: 0; }
  html, body {
    width: 1200px; height: 852px; overflow: hidden;
    background: var(--stage);
    font-family: "Roboto", Arial, sans-serif;
  }
  .canvas {
    position: relative; width: 1200px; height: 852px;
    display: flex; align-items: center; justify-content: center; gap: 40px;
  }
  .card {
    position: relative; width: 520px; height: 300px;
    border-radius: 24px; overflow: hidden;
    box-shadow: 0 18px 40px rgba(0,0,0,.55);
  }
  .card-waves { position: absolute; inset: 0; width: 100%; height: 100%; }
  .brand {
    position: absolute; color: var(--white); font-weight: 300;
    text-align: center; line-height: 1;
  }
  .brand-name { display: block; letter-spacing: 2px; }
  .brand-tagline { display: block; letter-spacing: 7px; text-transform: lowercase; }
  .card-front .brand { left: 0; right: 0; top: 92px; }
  .card-front .brand-name { font-size: 92px; }
  .card-front .brand-tagline { font-size: 13px; margin-top: 14px; }
  .card-back .brand { right: 34px; top: 22px; text-align: right; }
  .card-back .brand-name { font-size: 62px; }
  .card-back .brand-tagline { font-size: 10px; margin-top: 8px; letter-spacing: 5px; }
  .contact {
    position: absolute; right: 30px; top: 122px; text-align: right; color: var(--white);
  }
  .contact-name { font-size: 19px; font-weight: 700; line-height: 22px; }
  .contact-title { font-size: 12px; font-weight: 300; line-height: 14px; margin-bottom: 14px; color: var(--ice-blue); }
  .contact-list { list-style: none; }
  .contact-item {
    display: flex; justify-content: flex-end; align-items: center; gap: 10px;
    font-size: 12px; font-weight: 300; height: 17px; color: var(--ice-blue);
  }
  .contact-icon { width: 12px; height: 12px; flex: none; }
</style>
</head>
<body>
<main class="canvas">

  <section class="card card-front" aria-label="Business card front">
    <svg class="card-waves" viewBox="0 0 520 300" preserveAspectRatio="none" aria-hidden="true">
      <defs>
        <linearGradient id="front-base" x1="0" y1="0" x2="0" y2="1">
          <stop offset="0" stop-color="#0a6fb8"/>
          <stop offset="1" stop-color="#063F86"/>
        </linearGradient>
      </defs>
      <rect width="520" height="300" fill="url(#front-base)"/>
      <path d="M0 0H520V40C420 90 300 20 180 70C110 100 50 80 0 120Z" fill="#2f9ed6"/>
      <path d="M0 0H520V10C430 60 320 0 200 40C120 65 60 50 0 80Z" fill="#45b2df"/>
      <path d="M0 150C120 110 230 170 340 130C420 100 480 120 520 100V300H0Z" fill="#0a64ae" opacity=".8"/>
      <path d="M0 220C140 180 260 240 380 200C450 180 490 190 520 175V300H0Z" fill="#0054AA" opacity=".9"/>
    </svg>
    <div class="brand">
      <span class="brand-name">tbk</span>
      <span class="brand-tagline">plumbing services</span>
    </div>
  </section>

  <section class="card card-back" aria-label="Business card back">
    <svg class="card-waves" viewBox="0 0 520 300" preserveAspectRatio="none" aria-hidden="true">
      <defs>
        <linearGradient id="back-base" x1="0" y1="0" x2="1" y2="0">
          <stop offset="0" stop-color="#3aa9d9"/>
          <stop offset=".55" stop-color="#0677BA"/>
          <stop offset="1" stop-color="#0054AA"/>
        </linearGradient>
      </defs>
      <rect width="520" height="300" fill="url(#back-base)"/>
      <path d="M0 0H260C230 80 200 160 120 300H0Z" fill="#4fb6e0" opacity=".7"/>
      <path d="M300 0H520V300H220C300 200 330 100 300 0Z" fill="#0a5fa8" opacity=".75"/>
      <path d="M380 0H520V300H330C400 200 410 90 380 0Z" fill="#0054AA" opacity=".8"/>
      <path d="M0 300L520 260V268L30 300Z" fill="#1FA8E6"/>
      <path d="M30 300L520 268V300Z" fill="#0677BA"/>
    </svg>
    <div class="brand">
      <span class="brand-name">tbk</span>
      <span class="brand-tagline">plumbing services</span>
    </div>
    <div class="contact">
      <p class="contact-name">Rowan Keddle</p>
      <p class="contact-title">Director</p>
      <ul class="contact-list">
        <li class="contact-item">0431 286 517
          <svg class="contact-icon" viewBox="0 0 12 12" aria-hidden="true"><path d="M2 1h2.5l1 3-1.5 1a6 6 0 0 0 3 3l1-1.5 3 1V10a1 1 0 0 1-1 1A9 9 0 0 1 1 2a1 1 0 0 1 1-1z" fill="#fff"/></svg>
        </li>
        <li class="contact-item">rowan@tbk-plumbing.com.au
          <svg class="contact-icon" viewBox="0 0 12 12" aria-hidden="true"><rect x="1" y="2.5" width="10" height="7" fill="#fff"/><path d="M1 2.5l5 4 5-4" stroke="#0677BA" fill="none"/></svg>
        </li>
        <li class="contact-item">www.tbk-plumbing.com.au
          <svg class="contact-icon" viewBox="0 0 12 12" aria-hidden="true"><circle cx="6" cy="6" r="5" fill="#fff"/><path d="M1 6h10M6 1c-2.5 3-2.5 7 0 10M6 1c2.5 3 2.5 7 0 10" stroke="#0677BA" fill="none" stroke-width=".8"/></svg>
        </li>
        <li class="contact-item">ABN - 73 215 904 386
          <svg class="contact-icon" viewBox="0 0 12 12" aria-hidden="true"><path d="M4.5 1l-1 10M8.5 1l-1 10M1.5 4h9.5M1 8h9.5" stroke="#fff" stroke-width="1.2"/></svg>
        </li>
      </ul>
    </div>
  </section>

</main>
</body>
</html>
```